Business Cards for IT Consulting Company (Managed Service Provider)

I am looking to have some business cards printed and would like some designs. We are an IT Consulting company based in Vancouver BC. I would like a nice clean and modern look to the cards. I have uploaded all the versions of my logo so parts can be used as needed. Here is a snippit from our website homepage:

Quillbrook Networks Ltd. is an IT Solutions Partner located in Vancouver BC, Canada. We offer IT solutions and support to customers in the greater Vancouver Area. With expertise in Microsoft platforms, as well as Linux and Mac OSX and over 12 years experience in the IT industry, Quillbrook Networks is dedicated to offering our clients top quality service and products. We take pride in the solutions we offer our customers. The greatest compliment a client can give us is to recommend our services.

Quillbrook Networks Ltd. offers a wide range of IT services from onsite service to remote support and managed service solutions. This allows clients to choose the support path that best suits their company’s needs. Supporting many different sized companies from small to enterprise level over the past 12 years Quillbrook Networks has the experience and expertise needed to ensure things run smoothly. Allowing our clients to focus on doing business.

Revolutionizing the way IT services are delivered.

Quillbrook Networks is dedicated to providing our clients with IT solutions that work and grow with them for years to come. This philosophy helps save money in the long run instead of replacing equipment constantly. Far too often IT solutions are not well thought out and while possibly solving the problem at hand, require replacement due to growth or quality within a very short time frame. Quillbrook Networks takes pride in providing solutions that will last and be able to accommodate growth without the need for replacement.

Industry/Entity Type

Information Technology

Contact Information for Business Card

Quillbrook Networks Ltd.
(Employee Name)
Eml: (Employees Email Address)
Web: quillbrook.me
Ph: 604-555-0148

Font styles to use
Serif
Sans Serif

Requirements
Must have
• The Company logo and company colors.
Nice to have
• - Our tag line: "Revolutionizing IT Services" or "Revolutionizing the way IT services are delivered."
• - Also I really like the idea of nature and technology together blending which is sort of where my logo came from so integrating that somehow onto the business cards would be great.

```html
<!DOCTYPE html>
<html lang="en">
<head>
<meta charset="utf-8">
<title>Quillbrook Networks Ltd. — Business Card</title>
<link rel="stylesheet" href="https://fonts.googleapis.com/css2?family=Montserrat:wght@600&family=Roboto:ital,wght@0,400;0,500;1,400&display=swap">
<style>
  :root {
    --brand-blue: #1a90d4;
    --brand-grey: #505153;
    --text-dark: #3a3a3c;
    --card-white: #f7f7f7;
    --backdrop: #b4b3b3;
  }
  * { margin: 0; padding: 0; box-sizing: border-box; }
  html, body { width: 1200px; height: 1200px; overflow: hidden; }
  body { background: var(--backdrop); position: relative; font-family: "Roboto", Arial, sans-serif; }

  .card { position: absolute; background: var(--card-white); overflow: hidden; }
  .card--front { left: 238px; top: 118px; width: 712px; height: 420px; }
  .card--back { left: 231px; top: 644px; width: 712px; height: 416px; }

  .wordmark {
    position: absolute; display: flex; align-items: center; gap: 14px;
    font-family: "Montserrat", Arial, sans-serif; font-weight: 600;
    color: var(--brand-blue); white-space: nowrap;
  }
  .wordmark__square { width: 22px; height: 22px; background: var(--brand-blue); flex: none; }
  .card--front .wordmark { left: 0; right: 0; top: 162px; justify-content: center; font-size: 40px; }
  .card--back .wordmark { right: 40px; top: 58px; font-size: 27px; gap: 10px; }
  .card--back .wordmark__square { width: 16px; height: 16px; }

  .tagline-rule {
    position: absolute; left: 0; right: 0; top: 376px;
    display: flex; align-items: center; justify-content: center; gap: 16px;
    font-size: 19px; color: var(--text-dark); letter-spacing: 0.2px;
  }
  .tagline-rule__line { width: 110px; height: 3px; background: var(--brand-blue); border-radius: 2px; }

  .holder { position: absolute; left: 39px; top: 70px; }
  .holder__name { font-size: 25px; font-weight: 500; color: var(--brand-blue); }
  .holder__role { font-size: 16px; font-style: italic; color: var(--text-dark); margin-top: 4px; }

  .contact { position: absolute; left: 38px; top: 230px; list-style: none; }
  .contact__item { display: flex; align-items: center; gap: 16px; height: 27px; font-size: 17px; color: var(--text-dark); }
  .contact__icon { width: 18px; height: 14px; flex: none; fill: var(--brand-blue); }

  .wave { position: absolute; left: 0; top: 0; width: 712px; height: 416px; }
  .wave__grey { fill: var(--brand-grey); }
  .wave__blue { fill: var(--brand-blue); }

  .slogan {
    position: absolute; right: 31px; top: 336px; text-align: right;
    font-size: 17px; line-height: 25px; color: #ffffff;
  }
</style>
</head>
<body>
  <section class="card card--front" aria-label="Card front">
    <div class="wordmark"><span class="wordmark__square"></span>Quillbrook Networks Ltd.</div>
    <div class="tagline-rule">
      <span class="tagline-rule__line"></span>
      <span>Revolutionizing IT Services</span>
      <span class="tagline-rule__line"></span>
    </div>
  </section>

  <section class="card card--back" aria-label="Card back">
    <svg class="wave" viewBox="0 0 712 416" aria-hidden="true">
      <path class="wave__grey" d="M0,336 C120,350 260,326 400,262 C520,208 630,200 712,206 L712,226 C620,222 540,238 420,290 C300,342 150,372 0,364 Z"/>
      <path class="wave__blue" d="M0,374 C170,380 310,330 440,276 C560,228 640,230 712,236 L712,416 L0,416 Z"/>
    </svg>

    <div class="holder">
      <div class="holder__name">Daniel Morrow</div>
      <div class="holder__role">Managing Director</div>
    </div>

    <div class="wordmark"><span class="wordmark__square"></span>Quillbrook Networks Ltd.</div>

    <ul class="contact">
      <li class="contact__item">
        <svg class="contact__icon" viewBox="0 0 18 14" aria-hidden="true"><path d="M1 4 C1 1 17 1 17 4 L17 5 L13 5 L12 3 L6 3 L5 5 L1 5 Z M4 6 L14 6 L16 13 L2 13 Z"/></svg>
        <span>604-555-0148</span>
      </li>
      <li class="contact__item">
        <svg class="contact__icon" viewBox="0 0 18 14" aria-hidden="true"><circle cx="9" cy="7" r="6.3" fill="none" stroke="#1a90d4" stroke-width="1.4"/><ellipse cx="9" cy="7" rx="2.6" ry="6.3" fill="none" stroke="#1a90d4" stroke-width="1.2"/><path d="M2.7 7 H15.3" stroke="#1a90d4" stroke-width="1.2"/></svg>
        <span>www.quillbrook.me</span>
      </li>
      <li class="contact__item">
        <svg class="contact__icon" viewBox="0 0 18 14" aria-hidden="true"><path d="M1 2 H17 V12 H1 Z"/><path d="M1 2 L9 8 L17 2" fill="none" stroke="#f7f7f7" stroke-width="1.3"/></svg>
        <span>support@quillbrook.me</span>
      </li>
    </ul>

    <p class="slogan">Revolutionizing the<br>way IT services are delivered</p>
  </section>
</body>
</html>
```